New Innovative Counselling and psychotherapy Service needs Business Card design

Keep it simple and professional. On one side, just company name and logo (perhaps in all blue) and maybe a tag line.

On other side (all white) my name and Qualifications in centre

Industry/Entity Type

Health And Wellness

Contact Information for Business Card

Dara Whelby
Counsellor & Psychotherapist
BSc (Psychol.), BA, Dip. (Couns. & Psych.), PG.Cert (CBT), FGTrK, ONRE

I will also require Mobile no, Email and web site address of which I'll pass on to final designer.

Font styles to use
Sans Serif

Requirements
Must have
• My Logo Only and please use the colours in logo that is in it.
Should not have
• Any other images

```html
<!DOCTYPE html>
<html lang="en">
<head>
<meta charset="utf-8">
<title>Brightwell Row – Business Card</title>
<link rel="stylesheet" href="https://fonts.googleapis.com/css2?family=Arimo:wght@400;700&display=swap">
<style>
  :root {
    --sky: #45b0ea;
    --sky-deep: #2f9bd6;
    --leaf: #8cc63f;
    --ink: #3a3a3a;
    --ink-soft: #555555;
    --paper: #ffffff;
    --paper-tint: #f4f6f7;
    --backdrop: #e9ebed;
    --rule: #7a7a7a;
  }
  * { box-sizing: border-box; margin: 0; padding: 0; }
  html, body {
    width: 1200px; height: 950px; overflow: hidden;
    background: var(--backdrop);
    font-family: "Arimo", Arial, sans-serif;
  }
  .canvas {
    position: relative; width: 1200px; height: 950px;
  }
  .card {
    position: absolute; top: 145px;
    width: 400px; height: 660px;
    border-radius: 26px;
    overflow: hidden;
    box-shadow: 0 10px 28px rgba(0,0,0,0.12);
  }
  /* Front */
  .card--front {
    left: 150px;
    background: linear-gradient(160deg, var(--paper) 0%, var(--paper-tint) 100%);
  }
  .wordmark {
    position: absolute; top: 46px; left: 44px;
    display: flex; align-items: center; gap: 12px;
  }
  .wordmark__dot {
    width: 38px; height: 38px; border-radius: 50%;
    background: var(--sky);
  }
  .wordmark__name {
    font-size: 30px; font-weight: 400; color: var(--ink);
    letter-spacing: 0.5px;
  }
  .identity {
    position: absolute; left: 44px; right: 40px; top: 400px;
  }
  .identity__name {
    font-size: 32px; font-weight: 700; color: var(--sky);
    margin-bottom: 8px;
  }
  .identity__role,
  .identity__quals {
    font-size: 16px; color: var(--leaf); line-height: 1.3;
  }
  .identity__rule {
    height: 1px; background: var(--rule);
    margin: 18px 0 16px;
  }
  .contact { list-style: none; }
  .contact__item {
    display: flex; align-items: center; gap: 10px;
    font-size: 17px; color: var(--ink-soft);
    line-height: 1.55;
  }
  .contact__icon { width: 16px; height: 16px; flex: none; }
  /* Back */
  .card--back {
    left: 650px;
    background: var(--sky);
  }
  .back-mark {
    position: absolute; top: 50%; left: 50%;
    transform: translate(-50%, -50%);
    display: flex; flex-direction: column; align-items: center; gap: 20px;
  }
  .back-mark__dot {
    width: 150px; height: 150px; border-radius: 50%;
    background: var(--paper);
  }
  .back-mark__name {
    font-size: 34px; font-weight: 400; color: var(--paper);
    white-space: nowrap;
  }
  .tagline {
    position: absolute; left: 36px; top: 40px;
    transform-origin: left top;
    transform: rotate(90deg) translateY(-100%);
    font-size: 15px; color: var(--paper);
    white-space: nowrap; letter-spacing: 0.3px;
  }
</style>
</head>
<body>
<main class="canvas">
  <section class="card card--front" aria-label="Business card front">
    <div class="wordmark">
      <span class="wordmark__dot"></span>
      <span class="wordmark__name">Brightwell Row</span>
    </div>
    <div class="identity">
      <h1 class="identity__name">Dara Whelby</h1>
      <p class="identity__role">Counsellor &amp; Psychotherapist</p>
      <p class="identity__quals">BSc (Psychol.), BA, Dip. (Couns. &amp; Psych.)<br>PG.Cert (CBT), FGTrK.</p>
      <div class="identity__rule"></div>
      <ul class="contact">
        <li class="contact__item">
          <svg class="contact__icon" viewBox="0 0 16 16"><rect x="3" y="1" width="10" height="14" rx="2" fill="none" stroke="var(--sky)" stroke-width="1.8"/></svg>
          555 210 4837
        </li>
        <li class="contact__item">
          <svg class="contact__icon" viewBox="0 0 16 16"><rect x="1" y="3" width="14" height="10" rx="1" fill="var(--sky)"/><path d="M1 4l7 5 7-5" fill="none" stroke="var(--paper)" stroke-width="1.3"/></svg>
          dara@Brightwellrow.com
        </li>
        <li class="contact__item">
          <svg class="contact__icon" viewBox="0 0 16 16"><circle cx="8" cy="8" r="7" fill="var(--sky)"/><path d="M1 8h14M8 1c-3 3-3 11 0 14M8 1c3 3 3 11 0 14" fill="none" stroke="var(--paper)" stroke-width="1"/></svg>
          www.Brightwellrow.com
        </li>
      </ul>
    </div>
  </section>

  <section class="card card--back" aria-label="Business card back">
    <p class="tagline">Your Psychological Well-Being Is Our Top Priority</p>
    <div class="back-mark">
      <span class="back-mark__dot"></span>
      <span class="back-mark__name">Brightwell Row</span>
    </div>
  </section>
</main>
</body>
</html>
```